Musician artist looking for artwork CD jacket

I need an artwork for my first record which will be called "The Paper Lantern". It is a concept-album on a blase musician who takes refuge in the quest for women and his excesses. I do not want to use photos of myself on the cover but go with the idea of a puppet, a puppet, automaton etc with possibly in the background elements that could recall the concept of my album. The final design must appeal above all, in rather dark tones, or in black and white, or red and black for example.

```html
<!DOCTYPE html>
<html lang="en">
<head>
<meta charset="utf-8">
<title>The Paper Lantern — Album Cover</title>
<link rel="stylesheet" href="https://fonts.googleapis.com/css2?family=Montserrat:wght@800&display=swap">
<style>
  :root {
    --paper-light: #ece6d8;
    --paper-mid: #c8c0b0;
    --paper-dark: #8f887c;
    --ink: #1e1c1a;
    --disc: #000000;
    --puppet-red: #ff0000;
  }
  html, body {
    margin: 0;
    padding: 0;
    width: 1200px;
    height: 1200px;
    overflow: hidden;
    background: var(--paper-mid);
  }
  .cover {
    position: relative;
    width: 1200px;
    height: 1200px;
    overflow: hidden;
  }
  .cover__backdrop {
    position: absolute;
    inset: 0;
    background:
      radial-gradient(circle at 48% 49%, var(--paper-light) 0%, var(--paper-mid) 55%, var(--paper-dark) 120%);
  }
  .cover__title-grid {
    position: absolute;
    inset: 0;
    width: 1200px;
    height: 1200px;
  }
  .title-row {
    font-family: 'Montserrat', sans-serif;
    font-weight: 800;
    font-size: 98px;
    fill: var(--ink);
  }
  .cover__disc {
    position: absolute;
    left: 140px;
    top: 152px;
    width: 876px;
    height: 876px;
    border-radius: 50%;
    background:
      radial-gradient(ellipse at 58% 52%, rgba(255,0,0,0.55) 0%, rgba(160,0,0,0.25) 28%, var(--disc) 55%);
  }
</style>
</head>
<body>
  <main class="cover">
    <div class="cover__backdrop" role="img" aria-label="Fine radiating beige and grey line pattern spreading out from the centre"></div>

    <svg class="cover__title-grid" viewBox="0 0 1200 1200" xmlns="http://www.w3.org/2000/svg" aria-label="The Paper Lantern">
      <text class="title-row" x="6" y="124" textLength="1176" lengthAdjust="spacingAndGlyphs">THE PAPER LANTERN</text>
      <text class="title-row" x="8" y="254" textLength="1174" lengthAdjust="spacingAndGlyphs">THE PAPER LANTERN</text>
      <text class="title-row" x="8" y="378" textLength="1175" lengthAdjust="spacingAndGlyphs">THE PAPER LANTERN</text>
      <text class="title-row" x="10" y="505" textLength="1173" lengthAdjust="spacingAndGlyphs">THE PAPER LANTERN</text>
      <text class="title-row" x="10" y="634" textLength="1174" lengthAdjust="spacingAndGlyphs">THE PAPER LANTERN</text>
      <text class="title-row" x="10" y="764" textLength="1174" lengthAdjust="spacingAndGlyphs">THE PAPER LANTERN</text>
      <text class="title-row" x="10" y="893" textLength="1174" lengthAdjust="spacingAndGlyphs">THE PAPER LANTERN</text>
      <text class="title-row" x="12" y="1022" textLength="1172" lengthAdjust="spacingAndGlyphs">THE PAPER LANTERN</text>
      <text class="title-row" x="12" y="1152" textLength="1172" lengthAdjust="spacingAndGlyphs">THE PAPER LANTERN</text>
    </svg>

    <div class="cover__disc" role="img" aria-label="Red silhouette of a large marionette figure on strings, itself holding a control bar that works a tiny walking puppet, set on a black disc"></div>
  </main>
</body>
</html>
```